Lottery Website Design

Full website design, where you can take part on a lottery. Inkl Logo. The website is already developed: http://www.zorbel-ziehung.de
I like the modern fullscreen design from
http://www.marvestaplay.com/en-us/home.html
but the field for using the lottery right away should be present as well an the first screen like here:
https://www.glueckspfade.de/spiel/
Colour Scheme:
Red and Yellow?
Responsive design and coding (HTML & CSS).
The current website layout with bootstrap design ist http://www.zorbel-ziehung.de - the logo may be similar to favicon
Feel free to ask! :)
As always I am looking forward for your great ideas!
Updates
Reason: Not yet the best result found ...

```html
<!DOCTYPE html>
<html lang="en">
<head>
<meta charset="utf-8">
<title>Zorbel Ziehung – Play Now &amp; Win</title>
<link href="https://fonts.googleapis.com/css2?family=Montserrat:wght@300;400;500;600;700&family=Roboto+Condensed:wght@400&display=swap" rel="stylesheet">
<style>
:root{
  --red:#c4161c;
  --red-dark:#a50f14;
  --maroon:#4a0406;
  --orange:#f7941d;
  --orange-light:#fdb813;
  --yellow:#fbc315;
  --ink:#333;
  --grey:#777;
  --light:#e8e8e8;
  --footer:#e6e6e6;
  --white:#fff;
}
*{box-sizing:border-box;margin:0;padding:0}
html,body{width:794px;height:1200px;overflow:hidden}
body{font-family:"Montserrat",sans-serif;color:var(--ink);background:var(--white);position:relative}
a{color:inherit;text-decoration:none}

.hero{position:absolute;left:0;top:0;width:794px;height:409px;
  background:radial-gradient(ellipse at 50% 55%,#d9252b 0%,#c4161c 45%,#8f0c10 100%);overflow:hidden}
.hero__cap{position:absolute;left:0;top:0;width:794px;height:80px}
.topbar{position:absolute;top:27px;left:86px;font-size:8.5px;color:#f3d5d5}
.topbar span{margin:0 7px}
.account{position:absolute;top:25px;right:76px;display:flex;gap:4px}
.account a{background:var(--red);color:#fff;font-size:8px;font-weight:700;padding:3px 8px;border-radius:2px}
.nav{position:absolute;top:75px;font-size:10.5px;font-weight:700;color:#fff;display:flex;gap:22px}
.nav--left{left:84px}
.nav--right{left:505px;gap:14px}
.logo{position:absolute;left:310px;top:48px;width:174px;height:71px;background:var(--maroon);
  border-radius:0 0 14px 14px;text-align:center;color:#fff}
.logo__name{display:flex;justify-content:center;align-items:center;gap:5px;margin-top:18px;font-size:18px;font-weight:500;letter-spacing:.5px}
.logo__dot{width:8px;height:8px;border-radius:50%;background:var(--red)}
.logo__tag{font-size:6px;margin-top:6px;color:#f1dede}

.hero__text{position:absolute;left:128px;top:150px;color:#fff}
.hero__brand{font-size:40px;font-weight:300;line-height:1}
.hero__sub{font-size:27px;font-weight:300;line-height:1.1;margin-top:4px}
.hero__prize{font-size:32px;font-weight:700;line-height:1.1}
.hero__draw{font-size:13px;font-weight:300;margin-top:18px}
.hero__time{font-size:12px;font-weight:600;margin-top:5px}
.btn-buy{display:inline-block;margin-top:12px;background:var(--yellow);color:#fff;font-weight:700;font-size:11.5px;padding:7px 13px}
.hero__art{position:absolute;left:395px;top:162px;width:262px;height:214px;border-radius:50%;
  background:radial-gradient(circle at 45% 50%,#e8323a 0%,#b3151b 40%,rgba(200,160,60,.45) 65%,rgba(196,22,28,0) 72%)}
.dots{position:absolute;top:386px;left:371px;display:flex;gap:6px}
.dots i{width:9px;height:9px;border-radius:50%;background:#fff}
.dots i:first-child{background:#5a0a0c}

.stage{position:absolute;left:0;top:409px;width:794px;height:560px;
  background:radial-gradient(ellipse at 50% 40%,var(--orange-light) 0%,var(--orange) 65%,#f07c10 100%)}
.curve{position:absolute;left:0;top:905px;width:794px;height:70px}

.play{position:absolute;left:85px;top:453px;width:415px;height:422px;background:#fff}
.play__head{height:46px;background:var(--red);color:#fff;font-size:19px;font-weight:300;padding:11px 16px}
.play__head b{font-weight:700}
.grid{position:absolute;left:7px;top:64px;width:401px;height:136px;border:1px solid #ececec;border-radius:3px;
  display:grid;grid-template-columns:repeat(6,1fr);grid-template-rows:1fr 1fr;padding:3px 5px}
.grid span{display:flex;align-items:center;justify-content:center;font-size:44px;font-weight:700;color:#cfcfcf;
  margin:2px;border:1px solid #f0f0f0;letter-spacing:-2px}
.label{position:absolute;font-size:9px;font-weight:600;color:#444}
.chip{position:absolute;display:flex;gap:5px}
.chip span{border:1px solid #ddd;font-size:8.5px;color:#999;padding:3px 5px;min-width:17px;text-align:center}
.chip span.on{background:var(--red);color:#fff;border-color:var(--red)}
.input{position:absolute;border:1px solid #ddd;font-size:8.5px;color:#999;padding:3px 5px}
.toggle{position:absolute;display:flex;gap:10px}
.toggle span{width:38px;height:17px;font-size:9px;color:#fff;text-align:center;line-height:17px}
.toggle .yes{background:#444}.toggle .no{background:var(--red)}
.ticket{position:absolute;left:18px;top:357px;display:flex;gap:2px}
.digit{width:31px;text-align:center}
.digit i,.digit em{display:block;height:7px;background:#3a3a3a;color:#fff;font-size:6px;line-height:7px;font-style:normal}
.digit b{display:block;font-size:9px;font-weight:400;padding:4px 0 3px;color:#444}
.digit.first i,.digit.first em{background:var(--red)}
.more{position:absolute;left:19px;top:410px;font-size:9px;color:#333}
.stake{position:absolute;left:266px;top:335px;width:149px;height:87px;background:var(--red);color:#fff;padding:10px 9px}
.stake__label{font-size:9px;font-weight:700}
.stake__field{margin-top:7px;border:1px solid #e05a5e;border-radius:2px;font-size:9.5px;font-weight:700;padding:5px 6px}
.stake__btn{display:inline-block;margin-top:7px;background:#3a0506;font-size:7.5px;font-weight:700;padding:4px 10px}

.ads__label{position:absolute;left:509px;top:459px;font-size:11px;font-weight:700;color:#fff}
.ad{position:absolute;left:509px;top:478px;width:198px;height:397px;
  background:linear-gradient(180deg,#1a5f8a 0%,#2f6f98 40%,#5c7f96 62%,#1f3850 100%);color:#fff;text-align:center}
.ad__title{font-family:"Roboto Condensed",sans-serif;font-size:15px;margin-top:36px}
.ad__sub{font-size:7px;font-weight:500;text-align:right;padding-right:17px;margin-top:7px}
.ad__photo{position:absolute;left:0;top:105px;width:198px;height:175px;
  background:linear-gradient(160deg,rgba(255,255,255,.15),rgba(160,170,180,.55) 50%,rgba(30,60,90,.3))}
.ad__dealer{position:absolute;left:22px;top:320px;display:flex;align-items:center;gap:9px;text-align:left}
.ad__ring{width:34px;height:34px;border:2px solid #fff;border-radius:50%}
.ad__name{font-family:"Roboto Condensed",sans-serif;font-size:15px;line-height:1.05}
.ad__name small{display:block;font-size:9px}
.ad__fine{position:absolute;left:0;width:100%;top:380px;font-size:4.5px}

.why{position:absolute;left:0;top:945px;width:794px;text-align:center}
.why h2{font-size:19px;font-weight:600;color:#333}
.why p{width:624px;margin:16px auto 0;font-size:9px;line-height:16px;color:#444;font-weight:400}
.why p b{font-weight:700}
.cta{display:flex;justify-content:center;gap:6px;margin-top:20px}
.cta a{width:99px;height:29px;line-height:29px;color:#fff;font-weight:700;font-size:12px}
.cta .login{background:#1c1c1c}.cta .register{background:var(--red)}

.footer{position:absolute;left:0;top:1137px;width:794px;height:63px;background:var(--footer)}
.footer__copy{position:absolute;left:83px;top:26px;font-size:9px;color:#444}
.social{position:absolute;left:641px;top:22px;display:flex;gap:9px}
.social span{width:16px;height:16px;background:#3a3a3a;border-radius:2px}
</style>
</head>
<body>

<header class="hero">
  <svg class="hero__cap" viewBox="0 0 794 80" preserveAspectRatio="none" aria-hidden="true">
    <path d="M0 0H794V55Q600 40 484 46V0H310V46Q190 40 0 74Z" fill="#3d0305"/>
  </svg>
  <div class="topbar"><a href="#">Get Email Updates</a><span>|</span><a href="#">Retailer Locator</a></div>
  <div class="account"><a href="#">Login</a><a href="#">Register</a></div>
  <nav class="nav nav--left"><a href="#">HOME</a><a href="#">ABOUT US</a><a href="#">PLAY NOW</a></nav>
  <div class="logo">
    <div class="logo__name"><span class="logo__dot"></span>ZORBEL ZIEHUNG</div>
    <div class="logo__tag">Kostenlose Lotto-Simulation mit Kostenkontrolle</div>
  </div>
  <nav class="nav nav--right"><a href="#">FAQ'S</a><a href="#">PROMOTIONS</a><a href="#">CONTACT US</a></nav>

  <div class="hero__text">
    <div class="hero__brand">Zorbel Ziehung</div>
    <div class="hero__sub">Play Now &amp; Win</div>
    <div class="hero__prize">$ 6,000,000</div>
    <div class="hero__draw">Next Draw: Sat, Jul 19</div>
    <div class="hero__time">9:59 PM CST</div>
    <a class="btn-buy" href="#">BUY NOW</a>
  </div>
  <div class="hero__art" role="img" aria-label="Illustration of colourful numbered bingo balls on bingo cards"></div>
  <div class="dots"><i></i><i></i><i></i><i></i></div>
</header>

<section class="stage"></section>
<svg class="curve" viewBox="0 0 794 70" preserveAspectRatio="none" aria-hidden="true">
  <path d="M0 56Q397 -20 794 56V70H0Z" fill="#fff"/>
</svg>

<section class="play">
  <div class="play__head">Zorbel Ziehung <b>Play Now &amp; Win</b></div>
  <div class="grid">
    <span>1</span><span>2</span><span>3</span><span>4</span><span>5</span><span>6</span>
    <span>7</span><span>8</span><span>9</span><span>10</span><span>11</span><span>12</span>
  </div>

  <div class="label" style="left:12px;top:221px">Quicktipps (Zufallszahlen)</div>
  <div class="chip" style="left:12px;top:240px"><span>+1</span><span>+1</span><span>+1</span><span>+1</span><span>+1</span></div>

  <div class="label" style="left:166px;top:221px">Drawing</div>
  <div class="chip" style="left:165px;top:240px"><span>Mi</span><span>Sa</span><span style="width:45px;text-align:left">Mi/sa</span></div>

  <div class="label" style="left:308px;top:221px">Week Duration</div>
  <div class="chip" style="left:308px;top:240px"><span class="on">1</span><span>2</span><span>3</span><span>4</span></div>

  <div class="label" style="left:166px;top:284px">Ziehungstag</div>
  <div class="input" style="left:165px;top:302px;width:90px">Sa, 17-7-2014</div>

  <div class="label" style="left:308px;top:284px">Duration Coupon</div>
  <div class="toggle" style="left:308px;top:302px"><span class="yes">Yes</span><span class="no">No</span></div>

  <div class="label" style="left:20px;top:345px">Ticket Number</div>
  <div class="ticket">
    <div class="digit first"><i>&#9650;</i><b>3</b><em>&#9660;</em></div>
    <div class="digit"><i>&#9650;</i><b>3</b><em>&#9660;</em></div>
    <div class="digit"><i>&#9650;</i><b>3</b><em>&#9660;</em></div>
    <div class="digit"><i>&#9650;</i><b>3</b><em>&#9660;</em></div>
    <div class="digit"><i>&#9650;</i><b>3</b><em>&#9660;</em></div>
    <div class="digit"><i>&#9650;</i><b>3</b><em>&#9660;</em></div>
    <div class="digit"><i>&#9650;</i><b>3</b><em>&#9660;</em></div>
  </div>
  <a class="more" href="#">Additional Lottries &gt;&gt;</a>

  <div class="stake">
    <div class="stake__label">Stake</div>
    <div class="stake__field">$0.00</div>
    <a class="stake__btn" href="#">PLAY THE LOTTERY</a>
  </div>
</section>

<div class="ads__label">Sponsored Ads</div>
<aside class="ad">
  <div class="ad__title">Benchmark in Sophistication.</div>
  <div class="ad__sub">THE ALL-NEW 2014 V-SERIES</div>
  <div class="ad__photo" role="img" aria-label="Photo of a silver luxury saloon car driving at speed"></div>
  <div class="ad__dealer">
    <span class="ad__ring"></span>
    <div class="ad__name">Valcourt Motors<small>of Harborside</small></div>
  </div>
  <div class="ad__fine">PREPRODUCTION VEHICLE SHOWN WITH OPTIONAL AND EXTRA EQUIPMENT</div>
</aside>

<section class="why">
  <h2>Why not a lottery?</h2>
  <p>Every week on Wednesday and Saturday Lotto numbers are drawn. Average 21 million German then wait for that exact their numbers are drawn from the Lottofee. Nevertheless, the chance of winning only 1:140 million. Six Degrees with super number is less likely than being hit by lightning. Even a profit, just use the game brings back, has a chance of not even two Prozent.Trotzdem get millions of people lottery tickets and dream of the big jackpot. Each week money to invest in a lottery ticket seems to be not a large sum, and now and then you win even a small sum which at least einspielt the current use again; maybe even something more? <b>... Read More</b></p>
  <div class="cta"><a class="login" href="#">LOGIN</a><a class="register" href="#">REGISTER</a></div>
</section>

<footer class="footer">
  <div class="footer__copy">Copyright 2014 ,Zorbel-Ziehung.de All Rights Reserved</div>
  <div class="social" aria-label="Social links"><span></span><span></span><span></span></div>
</footer>

</body>
</html>
```